Stationery Design Project

Hi All,

We need you to design stationary for a new Business and Accounting Advisory Firm. We have already got the logo designed and it is attached. If you could also if possible, match the fonts in your design to that on the logo’s provided.

What we need:
- Business Card
- A4 Letter head
- A4 Folders
- PPT template (Title page and regular page)

And what ever else you want to throw in.

We are in the process of getting the web site designed, however below is a list of websites which we like which will give you an understanding of the style that we are going for.

- plivant.example
- moldrabay.example
- tarvenhook.example
- quillorbank.example

I look forward to your seeing your design.
Updates

Hi All,

I have just realised that I forgot that i need to include a Sworn Ledgerkeepers image on the letter head, please find attaced as File 1. Could you please have this image in the bottom left header.

Regards,

Marcus

Industry/Entity Type

Business

Requirements
Must have
• Outputs:
- Documents ready to print
- Generic editable information
- Pdf copies of the documents
- Word version of letterhead

```html
<!DOCTYPE html>
<html lang="en">
<head>
<meta charset="utf-8">
<title>Ostrelle Partners – Envelope</title>
<link rel="stylesheet" href="https://fonts.googleapis.com/css2?family=EB+Garamond:wght@500&family=Open+Sans:wght@400&display=swap">
<style>
  :root {
    --navy: #34508f;
    --ink: #2f4f8a;
    --brand-blue: #3d8fd0;
    --orange: #f07f22;
    --yellow: #f7c52c;
    --deep-blue: #2c4c8c;
    --cyan: #3ab6e0;
    --paper: #ffffff;
  }
  html, body {
    margin: 0;
    padding: 0;
    overflow: hidden;
    background: var(--paper);
  }
  .envelope {
    position: relative;
    width: 1200px;
    height: 521px;
    background: var(--paper);
    overflow: hidden;
  }
  .brand {
    position: absolute;
    left: 22px;
    top: 24px;
    display: flex;
    align-items: center;
    gap: 22px;
  }
  .brand-dot {
    width: 104px;
    height: 104px;
    border-radius: 50%;
    background: var(--brand-blue);
  }
  .brand-name {
    font-family: "EB Garamond", Georgia, serif;
    font-weight: 500;
    font-size: 46px;
    line-height: 1;
    color: var(--navy);
    letter-spacing: 0.2px;
  }
  .return-address {
    position: absolute;
    left: 21px;
    top: 132px;
    margin: 0;
    font-family: "Open Sans", Arial, sans-serif;
    font-style: normal;
    font-size: 15px;
    line-height: 21px;
    color: var(--ink);
  }
  .footer-rule {
    position: absolute;
    top: 497px;
    height: 5px;
  }
  .footer-rule--warm {
    left: 16px;
    width: 154px;
    background: linear-gradient(90deg, var(--orange), var(--yellow));
  }
  .footer-rule--cool {
    left: 428px;
    width: 110px;
    background: linear-gradient(90deg, var(--deep-blue), var(--cyan));
  }
  .website {
    position: absolute;
    left: 178px;
    top: 485px;
    font-family: "Open Sans", Arial, sans-serif;
    font-size: 17px;
    line-height: 24px;
    color: var(--navy);
  }
</style>
</head>
<body>
  <main class="envelope">
    <header class="brand">
      <span class="brand-dot" aria-hidden="true"></span>
      <span class="brand-name">Ostrelle Partners</span>
    </header>

    <address class="return-address">
      1234 Street Address<br>
      City, State 12345
    </address>

    <footer>
      <span class="footer-rule footer-rule--warm" aria-hidden="true"></span>
      <span class="website">www.ostrellepartners.example</span>
      <span class="footer-rule footer-rule--cool" aria-hidden="true"></span>
    </footer>
  </main>
</body>
</html>
```